Road Construction Company needs business cards

We would like a new business card designed for our business.

We're a road construction company based in Qld, Australia.

Can the business card please have the following information on it.

Name: Warren Halbeck
Position: General Manager
Phone: 0472 915 348
Email: Warren.halbeck@tovrin.com.au
Address: 87 Marrow Ave, Pendlebay, QLD, 4023
Website: www.tovrin.com.au

Visually we'd like the card to be professional and simple.

Attached is our logo.

Our website is www.tovrin.com.au

Target Market(s)

Men aged 25-60

Contact Information for Business Card

As listed in project description

Font styles to use
Serif

Requirements
Must have
• Large logo on back of card

```html
<!DOCTYPE html>
<html lang="en">
<head>
<meta charset="utf-8">
<title>Tovrin Business Card</title>
<link rel="stylesheet" href="https://fonts.googleapis.com/css2?family=Fira+Sans:wght@400;600;800&display=swap">
<style>
  :root {
    --backdrop: #8e9194;
    --paper: #ffffff;
    --brand-blue: #0353a4;
    --accent-blue: #2ea3dc;
    --ink-light: #ffffff;
  }
  * { margin: 0; padding: 0; box-sizing: border-box; }
  html, body {
    width: 1200px; height: 1200px; overflow: hidden;
    background: var(--backdrop);
    font-family: "Fira Sans", sans-serif;
  }
  .canvas { position: relative; width: 1200px; height: 1200px; }

  .card {
    position: absolute;
    width: 635px; height: 403px;
    background: var(--paper);
    overflow: hidden;
  }
  .card--front { left: 156px; top: 151px; }
  .card--back { left: 373px; top: 673px; }

  .brand-name {
    position: absolute;
    left: 0; right: 0; top: 160px;
    text-align: center;
    font-weight: 800;
    font-size: 58px;
    letter-spacing: 2px;
    line-height: 1;
    color: var(--brand-blue);
  }

  .identity { position: absolute; left: 0; right: 0; top: 56px; text-align: center; }
  .identity__name {
    font-weight: 600; font-size: 24px; color: var(--brand-blue);
    letter-spacing: 0.3px; line-height: 1.1;
  }
  .identity__role {
    font-weight: 400; font-size: 19px; color: var(--accent-blue);
    margin-top: 3px; letter-spacing: 0.3px;
  }

  .contact-band {
    position: absolute; left: 0; right: 0; top: 168px; bottom: 0;
    background: var(--brand-blue);
  }
  .contact-band__strip {
    position: absolute; left: 0; right: 0; bottom: 0; height: 7px;
    background: var(--accent-blue);
  }

  .icon-row { position: absolute; left: 0; top: 0; width: 635px; height: 403px; }

  .contact-list {
    position: absolute; left: 0; right: 0; top: 236px;
    list-style: none; text-align: center;
    color: var(--ink-light); font-size: 15.5px; letter-spacing: 0.2px;
  }
  .contact-list li { height: 27.5px; line-height: 20px; }
</style>
</head>
<body>
<main class="canvas">

  <section class="card card--front" aria-label="Card front">
    <div class="brand-name">TOVRIN</div>
  </section>

  <section class="card card--back" aria-label="Card back">
    <div class="identity">
      <p class="identity__name">WARREN HALBECK</p>
      <p class="identity__role">General Manager</p>
    </div>

    <div class="contact-band"><div class="contact-band__strip"></div></div>

    <svg class="icon-row" viewBox="0 0 635 403" aria-hidden="true">
      <g fill="#0353a4" stroke="#ffffff" stroke-width="2.5">
        <circle cx="225" cy="168" r="20"/>
        <circle cx="287" cy="168" r="20"/>
        <circle cx="348" cy="168" r="20"/>
        <circle cx="410" cy="168" r="20"/>
      </g>
      <!-- phone -->
      <g fill="#ffffff">
        <path d="M214 164 q11 -9 22 0 l-2 4 h-4 l-1 -3 q-4 -1 -8 0 l-1 3 h-4 z"/>
        <path d="M218 168 h14 l2 7 h-18 z"/>
      </g>
      <circle cx="225" cy="171" r="2" fill="#0353a4"/>
      <!-- mail -->
      <g>
        <rect x="277" y="161" width="20" height="14" fill="#ffffff"/>
        <path d="M277 161 l10 8 l10 -8 M277 175 l7 -6 M297 175 l-7 -6" fill="none" stroke="#0353a4" stroke-width="1.3"/>
      </g>
      <!-- globe -->
      <g fill="none" stroke="#ffffff" stroke-width="1.8">
        <circle cx="347" cy="167" r="9"/>
        <ellipse cx="347" cy="167" rx="4" ry="9"/>
        <line x1="338" y1="167" x2="356" y2="167"/>
        <line x1="340" y1="162" x2="354" y2="162"/>
        <line x1="340" y1="172" x2="354" y2="172"/>
      </g>
      <path d="M350 168 l8 8 h-3 l2 4 -2 1 -2 -4 -3 2 z" fill="#ffffff"/>
      <!-- pin -->
      <path d="M410 180 q-9 -10 -9 -15 a9 9 0 0 1 18 0 q0 5 -9 15 z" fill="#ffffff"/>
      <circle cx="410" cy="165" r="3.5" fill="#0353a4"/>
    </svg>

    <ul class="contact-list">
      <li>0472 915 348</li>
      <li>Warren.halbeck@tovrin.com.au</li>
      <li>www.tovrin.com.au</li>
      <li>87 Marrow Ave, Pendlebay, QLD, 4023</li>
    </ul>
  </section>

</main>
</body>
</html>
```